job report

Designer – Professional Plumbing Job Report Template

Overview

We are seeking a skilled designer to create a professional, easy-to-use Job Report template for a commercial and maintenance plumbing business.
The report will be used for clients, property managers, facilities managers, strata, and retail centres and must clearly communicate findings, works completed, and recommendations in a polished, compliant, and branded format.

The final document must be suitable for PDF delivery, email, and ongoing reuse.

Objectives

Present plumbing works in a clear, professional, and defensible report format

Improve client understanding of findings and recommendations

Provide a repeatable template that can be used across maintenance, reactive, and investigative works

Allow easy insertion of text, tables, and photos

Report Structure (Minimum Inclusions)
1. Cover Page

Company logo and branding

Report title (e.g. Plumbing Job Report / Investigation Report)

Client name

Site address

Job reference / work order number

Date of attendance

Technician / contractor name

2. Client & Site Details

Client / company name

Site address

Contact person

Contact details

Access notes (after-hours, tenant access, etc.)

3. Reason for Attendance

Clear description of why attendance was required

Call-out type (reactive, scheduled maintenance, investigation, emergency, etc.)

Reported issue or scope requested by client

4. Findings / Observations

Detailed findings discovered on site

Condition of pipework, fixtures, drainage, or systems

Any contributing factors identified

Notes on compliance, wear, damage, or risk

(This section should support bullet points and paragraphs.)

5. Works Carried Out

Step-by-step description of works completed

Equipment used (e.g. jetter, CCTV camera, leak detection, flex shaft, etc.)

Repairs, replacements, testing, and verification

Confirmation that systems were tested and operational on completion

6. Photos & Visual Evidence

Clearly labelled photo sections

Before / during / after photos

Space for photo captions and explanations

Logical layout that aligns photos with written findings

7. Recommendations

Clearly separated from works completed

Urgent vs non-urgent recommendations

Preventative maintenance advice

Upgrade or replacement suggestions

Risk-based language where appropriate

8. Limitations & Exclusions

Areas not inspected

Access limitations

Assumptions made during inspection

Items outside scope of works

9. Conclusion

Summary of outcome

Confirmation of current system status

Next steps (if any)

10. Sign-Off

Contractor / technician name

Company name

Date

Optional client acknowledgement section

Design Requirements

Clean, professional layout

Commercial / trade-appropriate styling (not overly creative)

Easy-to-read fonts

Consistent headings and spacing

Logical flow for busy property managers

Editable format (Word / Google Docs / InDesign source file)

Final export-ready PDF version

Bonus (Nice to Have)

Traffic-light system (Green / Amber / Red) for condition reporting

Iconography for findings, repairs, and recommendations

Optional sections for compliance notes (AS/NCC references)

Space for QR codes or job reference numbers

Deliverables

Editable master report template

PDF version

Instructions or notes for ongoing use

```html
<!DOCTYPE html>
<html lang="en">
<head>
<meta charset="UTF-8">
<title>Tidewell Plumbing – Plumbing Job Report Cover</title>
<link rel="stylesheet" href="https://fonts.googleapis.com/css2?family=Outfit:wght@500;600;700&display=swap">
<style>
  :root {
    --cover-blue: #0b1fe4;
    --cover-blue-deep: #0818d6;
    --glow-centre: #5f6f9c;
    --glow-mid: #2f44d8;
    --brand-cyan: #52f2ec;
    --text-white: #ffffff;
    --rule-white: #ffffff;
  }

  * { margin: 0; padding: 0; box-sizing: border-box; }

  html, body {
    width: 856px;
    height: 1200px;
    overflow: hidden;
    background: var(--cover-blue);
  }

  .cover {
    position: relative;
    width: 856px;
    height: 1200px;
    overflow: hidden;
    font-family: "Outfit", "Century Gothic", sans-serif;
    color: var(--text-white);
    background: var(--cover-blue);
  }

  .cover-backdrop {
    position: absolute;
    inset: 0;
    background:
      radial-gradient(circle at 429px 318px,
        var(--glow-centre) 0px,
        #4a5cb8 110px,
        var(--glow-mid) 220px,
        var(--cover-blue) 330px),
      linear-gradient(180deg, var(--cover-blue) 0%, var(--cover-blue-deep) 100%);
  }

  .brand-mark {
    position: absolute;
    top: 196px;
    left: 0;
    width: 100%;
    text-align: center;
    color: var(--brand-cyan);
    font-weight: 700;
    line-height: 1;
  }

  .brand-name {
    display: block;
    font-size: 112px;
    letter-spacing: 2px;
  }

  .brand-trade {
    display: block;
    margin-top: 38px;
    font-size: 62px;
    letter-spacing: 6px;
  }

  .report-title {
    position: absolute;
    top: 580px;
    left: 0;
    width: 100%;
    text-align: center;
    font-weight: 600;
    font-size: 45px;
    line-height: 56px;
    letter-spacing: 0.5px;
    text-shadow: 2px 3px 3px rgba(0, 0, 60, 0.55);
  }

  .cover-fields {
    position: absolute;
    top: 780px;
    left: 127px;
    width: 602px;
    list-style: none;
  }

  .cover-field {
    display: flex;
    align-items: flex-end;
    height: 34px;
    margin-bottom: 36px;
    font-weight: 500;
    font-size: 22.5px;
    white-space: nowrap;
  }

  .cover-field-line {
    flex: 1;
    margin-left: 11px;
    margin-bottom: 4px;
    border-bottom: 2px solid var(--rule-white);
  }
</style>
</head>
<body>
  <main class="cover">
    <div class="cover-backdrop" role="img" aria-label="Blue background with a soft glow and faint plumbing tools pattern"></div>

    <div class="brand-mark">
      <span class="brand-name">TIDEWELL</span>
      <span class="brand-trade">PLUMBING</span>
    </div>

    <h1 class="report-title">Plumbing Job Report /<br>Investigation Report</h1>

    <ul class="cover-fields">
      <li class="cover-field"><span class="cover-field-label">Client Name:</span><span class="cover-field-line"></span></li>
      <li class="cover-field"><span class="cover-field-label">Site address:</span><span class="cover-field-line"></span></li>
      <li class="cover-field"><span class="cover-field-label">Job reference / Work order number:</span><span class="cover-field-line"></span></li>
      <li class="cover-field"><span class="cover-field-label">Date of attendance:</span><span class="cover-field-line"></span></li>
      <li class="cover-field"><span class="cover-field-label">Technician / Contractor Name:</span><span class="cover-field-line"></span></li>
    </ul>
  </main>
</body>
</html>
```